Business Card Design

We have recently seen two business cards that caught our attention and think the designs would work for us. We are an accounting firm that serves small businesses in a variety of industries. Attached are the two business card that inspired us along with very rough layouts. We would like to see a professional layout using our company information.

Industry/Entity Type

Accounting

Contact Information for Business Card

Company Name - Marlowe Thistle
Address - 4182 Orlanby Lane, Suite 610, Houston, TX 77093
713-555-0187 - Main
281-555-0342 - Fax

Team Member Names, emails and phone numbers (see attachment)

```html
<!DOCTYPE html>
<html lang="en">
<head>
<meta charset="utf-8">
<title>Marlowe Thistle — Business Card</title>
<link rel="stylesheet" href="https://fonts.googleapis.com/css2?family=Aldrich&display=swap">
<style>
  :root {
    --bg: #e6e4e1;
    --card-dark: #3a3a3a;
    --card-light: #f7f7f7;
    --card-shade: #e9e9e9;
    --accent-grey: #b4b4b4;
    --ink-light: #ffffff;
    --ink-dark: #3c3c3c;
  }
  * { margin: 0; padding: 0; box-sizing: border-box; }
  html, body { width: 1200px; height: 900px; overflow: hidden; background: var(--bg); }
  body { font-family: "Aldrich", "Segoe UI", sans-serif; }

  .canvas { position: relative; width: 1200px; height: 900px; }

  .card {
    position: absolute;
    left: 250px;
    width: 700px;
    height: 400px;
    border-radius: 44px;
    overflow: hidden;
    box-shadow: 0 10px 24px rgba(0,0,0,0.18);
    background: var(--card-dark);
  }
  .card--front { top: 36px; }
  .card--back { top: 464px; display: flex; align-items: center; justify-content: center; }

  .card__shape { position: absolute; inset: 0; }

  .brand {
    position: absolute;
    display: flex;
    align-items: center;
    gap: 10px;
    text-transform: uppercase;
    letter-spacing: 1px;
    white-space: nowrap;
  }
  .brand__mark { width: 12px; height: 12px; flex: none; }
  .brand--front { left: 34px; top: 186px; color: var(--ink-dark); font-size: 21px; }
  .brand--front .brand__mark { background: var(--ink-dark); }
  .brand--back { position: static; color: var(--ink-light); font-size: 40px; gap: 12px; }
  .brand--back .brand__mark { background: var(--ink-light); width: 18px; height: 18px; }

  .contact {
    position: absolute;
    right: 40px;
    top: 36px;
    color: var(--ink-light);
    text-align: right;
  }
  .contact__name { font-size: 25px; letter-spacing: 1.5px; text-transform: uppercase; }
  .contact__title { font-size: 15px; letter-spacing: 1.5px; text-transform: uppercase; margin-top: 4px; }
  .contact__address { font-size: 15px; line-height: 1.45; margin-top: 34px; letter-spacing: 0.5px; }
  .contact__lines { list-style: none; margin-top: 30px; }
  .contact__line {
    display: flex; align-items: center; justify-content: flex-end; gap: 10px;
    font-size: 15px; letter-spacing: 0.8px; height: 26px;
  }
  .contact__line svg { width: 15px; height: 15px; flex: none; }
</style>
</head>
<body>
<main class="canvas">

  <section class="card card--front" aria-label="Business card front">
    <svg class="card__shape" viewBox="0 0 700 400" preserveAspectRatio="none" aria-hidden="true">
      <path d="M0 0 H300 Q372 200 318 400 H0 Z" fill="var(--accent-grey)"/>
      <path d="M0 0 H296 Q356 200 296 400 H0 Z" fill="var(--card-light)"/>
      <path d="M30 40 Q30 18 52 18 H270 Q320 200 272 382 H52 Q30 382 30 360 Z" fill="var(--card-shade)" opacity="0.55"/>
    </svg>

    <div class="brand brand--front">
      <span class="brand__mark"></span>
      <span class="brand__name">Marlowe Thistle</span>
    </div>

    <div class="contact">
      <p class="contact__name">Renata Calloway</p>
      <p class="contact__title">Financial Advisor</p>
      <p class="contact__address">4182 Orlanby Lane, Suite 610<br>Houston, TX 77093</p>
      <ul class="contact__lines">
        <li class="contact__line">713-555-0187
          <svg viewBox="0 0 16 16"><path d="M3 1.5l3 3-1.5 2c1 2 2.5 3.5 4.5 4.5l2-1.5 3 3-2 2C6.5 14 2 9.5 1.5 3.5z" fill="#fff"/></svg>
        </li>
        <li class="contact__line">832-555-0129
          <svg viewBox="0 0 16 16"><rect x="4" y="1" width="8" height="14" rx="1.5" fill="none" stroke="#fff" stroke-width="1.5"/><circle cx="8" cy="12.5" r="0.9" fill="#fff"/></svg>
        </li>
        <li class="contact__line">281-555-0342
          <svg viewBox="0 0 16 16"><rect x="2" y="6" width="12" height="8" fill="#fff"/><rect x="4" y="1.5" width="8" height="4" fill="none" stroke="#fff" stroke-width="1.3"/></svg>
        </li>
        <li class="contact__line">rcalloway@marlowethistle.com
          <svg viewBox="0 0 16 16"><rect x="1" y="3" width="14" height="10" fill="#fff"/><path d="M1 3l7 6 7-6" fill="none" stroke="var(--card-dark)" stroke-width="1.2"/></svg>
        </li>
        <li class="contact__line">www.marlowethistle.com
          <svg viewBox="0 0 16 16"><circle cx="8" cy="8" r="6.5" fill="none" stroke="#fff" stroke-width="1.3"/><ellipse cx="8" cy="8" rx="3" ry="6.5" fill="none" stroke="#fff" stroke-width="1"/><path d="M1.5 8h13" stroke="#fff" stroke-width="1"/></svg>
        </li>
      </ul>
    </div>
  </section>

  <section class="card card--back" aria-label="Business card back">
    <div class="brand brand--back">
      <span class="brand__mark"></span>
      <span class="brand__name">Marlowe Thistle</span>
    </div>
  </section>

</main>
</body>
</html>
```